Eye Catching Business Card for Optometrist

We've recently refreshed our logo and now we need a fresh and bold look for our business cards. We provide progressive ways to improve people's vision and protect their eye health.

Use our new logo as guidance into the colors to use. As far as style goes, I love how bold and eye catching the card is for Lanternfield Studio. Feel free to use your creative judgement.

Tagline: "Clearly the best for your vision."

pertinent info to include:

Dr. Marcus Velbrin
Optometrist

7258 Dunmore Ridge Blvd #215
Brantwell, MO 64172
(555) 382-9017

marc@brantwellfamilyeyecare.example
www.brantwellfamilyeyecare.example

```html
<!DOCTYPE html>
<html lang="en">
<head>
<meta charset="utf-8">
<title>Brantwell Family Eye Care – Business Card</title>
<link rel="stylesheet" href="https://fonts.googleapis.com/css2?family=PT+Sans:wght@400;700&family=Tinos:wght@400;700&display=swap">
<style>
  :root {
    --stage: #2b2b2d;
    --tan: #d3bb9c;
    --card-white: #ffffff;
    --brand-red: #c8202b;
    --ink: #3a3a3a;
    --ink-dark: #1e1e1e;
    --divider: #c9c9c9;
  }
  * { margin: 0; padding: 0; box-sizing: border-box; }
  html, body {
    width: 1200px;
    height: 750px;
    overflow: hidden;
    background: var(--stage);
  }
  .canvas {
    width: 1200px;
    height: 750px;
    display: flex;
    align-items: center;
    justify-content: center;
    gap: 40px;
  }
  .card {
    width: 540px;
    height: 309px;
    border-radius: 22px;
    position: relative;
    overflow: hidden;
    box-shadow: 0 10px 28px rgba(0,0,0,0.45);
  }

  /* Back side */
  .card-back {
    background: var(--tan);
    color: #fff;
    font-family: "PT Sans", Arial, sans-serif;
  }
  .back-brand {
    position: absolute;
    top: 92px;
    left: 0;
    right: 0;
    display: flex;
    flex-direction: column;
    align-items: center;
    gap: 12px;
  }
  .brand-square {
    width: 58px;
    height: 58px;
    background: #fff;
  }
  .back-brand .brand-name {
    font-size: 20px;
    font-weight: 700;
    letter-spacing: 0.5px;
    text-transform: uppercase;
    color: #fff;
  }
  .back-web {
    position: absolute;
    bottom: 34px;
    left: 0;
    right: 0;
    text-align: center;
    font-size: 15px;
    letter-spacing: 0.3px;
  }

  /* Front side */
  .card-front {
    background: var(--card-white);
    font-family: "Tinos", "Times New Roman", serif;
    color: var(--ink);
  }
  .front-brand {
    position: absolute;
    left: 30px;
    top: 0;
    bottom: 0;
    width: 200px;
    display: flex;
    flex-direction: column;
    align-items: center;
    justify-content: center;
    gap: 12px;
  }
  .front-brand .brand-square { background: var(--brand-red); width: 70px; height: 70px; }
  .front-brand .brand-name {
    font-family: "PT Sans", Arial, sans-serif;
    font-size: 19px;
    font-weight: 700;
    text-transform: uppercase;
    color: var(--brand-red);
    text-align: center;
    line-height: 1.15;
  }
  .divider {
    position: absolute;
    left: 240px;
    top: 95px;
    width: 1px;
    height: 120px;
    background: linear-gradient(to bottom, transparent, var(--divider), transparent);
    transform: rotate(-28deg);
  }
  .contact {
    position: absolute;
    left: 262px;
    top: 48px;
    right: 24px;
  }
  .person-name {
    font-size: 18px;
    font-weight: 700;
    color: var(--brand-red);
    line-height: 1.1;
  }
  .person-title {
    font-size: 11px;
    font-weight: 700;
    color: var(--ink-dark);
    margin-left: 10px;
  }
  .address {
    margin-top: 28px;
    margin-left: 30px;
    font-size: 11.5px;
    line-height: 1.35;
  }
  .contact-list {
    list-style: none;
    margin-top: 28px;
    margin-left: 30px;
    font-size: 11.5px;
    line-height: 1.45;
  }
  .contact-list li {
    display: flex;
    align-items: center;
    gap: 6px;
    white-space: nowrap;
  }
  .contact-icon { width: 12px; height: 12px; flex: none; }
</style>
</head>
<body>
<main class="canvas">

  <section class="card card-back" aria-label="Business card back">
    <div class="back-brand">
      <span class="brand-square"></span>
      <span class="brand-name">Brantwell Family Eye Care</span>
    </div>
    <p class="back-web">www.brantwellfamilyeyecare.example</p>
  </section>

  <section class="card card-front" aria-label="Business card front">
    <div class="front-brand">
      <span class="brand-square"></span>
      <span class="brand-name">Brantwell Family<br>Eye Care</span>
    </div>

    <span class="divider"></span>

    <div class="contact">
      <h1 class="person-name">Dr. Marcus Velbrin</h1>
      <p class="person-title">Optometrist</p>

      <p class="address">7258 Dunmore Ridge Blvd #215<br>Brantwell, MO 64172</p>

      <ul class="contact-list">
        <li>
          <svg class="contact-icon" viewBox="0 0 12 12" aria-hidden="true">
            <circle cx="6" cy="6" r="6" fill="var(--brand-red)"/>
            <path d="M3.2 3.6c.4-.5 1-.5 1.3 0l.5.8c.2.3.1.6-.1.8l-.3.3c.4.9 1 1.5 1.9 1.9l.3-.3c.2-.2.5-.3.8-.1l.8.5c.5.3.5.9 0 1.3-.6.6-1.4.7-2.3.2C4.9 8.3 3.7 7.1 3 5.9c-.5-.9-.4-1.7.2-2.3z" fill="#fff"/>
          </svg>
          (555) 382-9017
        </li>
        <li>
          <svg class="contact-icon" viewBox="0 0 12 12" aria-hidden="true">
            <circle cx="6" cy="6" r="6" fill="var(--brand-red)"/>
            <rect x="2.8" y="3.8" width="6.4" height="4.4" fill="#fff"/>
            <path d="M2.8 3.8L6 6.3l3.2-2.5" fill="none" stroke="var(--brand-red)" stroke-width="0.7"/>
          </svg>
          marc@brantwellfamilyeyecare.example
        </li>
        <li>
          <svg class="contact-icon" viewBox="0 0 12 12" aria-hidden="true">
            <circle cx="6" cy="6" r="6" fill="var(--brand-red)"/>
            <circle cx="6" cy="6" r="3.4" fill="none" stroke="#fff" stroke-width="0.8"/>
            <ellipse cx="6" cy="6" rx="1.4" ry="3.4" fill="none" stroke="#fff" stroke-width="0.7"/>
            <path d="M2.6 6h6.8" stroke="#fff" stroke-width="0.7"/>
          </svg>
          www.brantwellfamilyeyecare.example
        </li>
      </ul>
    </div>
  </section>

</main>
</body>
</html>
```